Tiskoro

We need a business card for our company is a holding for different business all are different we try to have some air of relax and fun in our projects we add pictures of the office to give you an idea od the mood of the business

Business

```html
<!DOCTYPE html>
<html lang="en">
<head>
<meta charset="utf-8">
<title>Tiskoro business card</title>
<link href="https://fonts.googleapis.com/css2?family=Saira:wght@400;500;700&display=swap" rel="stylesheet">
<style>
  :root {
    --bg: #e4e2df;
    --card: #ffffff;
    --yellow: #f7e83a;
    --brown: #5a3b22;
    --rule: #8a6a4e;
    --ink: #2b2b2b;
    --muted: #6b6b6b;
    --icon-line: #b9b9b9;
    --icon-fill: #e6d21f;
  }
  html, body {
    margin: 0;
    width: 1200px;
    height: 1057px;
    overflow: hidden;
    background: var(--bg);
    font-family: "Saira", sans-serif;
  }
  .card {
    position: absolute;
    left: 100px;
    top: 243px;
    width: 1000px;
    height: 571px;
    background: var(--card);
    box-shadow: 0 6px 24px rgba(0,0,0,.12);
  }
  .brand {
    position: absolute;
    left: 70px;
    top: 56px;
    display: flex;
    align-items: center;
    gap: 18px;
  }
  .brand-square {
    width: 64px;
    height: 64px;
    background: var(--yellow);
  }
  .brand-name {
    font-size: 56px;
    font-weight: 700;
    color: var(--brown);
    line-height: 1;
    letter-spacing: -1px;
  }
  .contact-frame {
    position: absolute;
    left: 70px;
    top: 214px;
    width: 860px;
    height: 310px;
    border: 2px solid var(--rule);
    border-radius: 44px;
    box-sizing: border-box;
  }
  .person {
    position: absolute;
    left: 40px;
    top: -34px;
    background: var(--card);
    padding: 0 16px;
  }
  .person-name {
    font-size: 40px;
    font-weight: 400;
    letter-spacing: 3px;
    color: var(--ink);
    line-height: 1.1;
    margin: 0;
  }
  .person-role {
    font-size: 15px;
    letter-spacing: 2px;
    color: var(--muted);
    margin: 0;
  }
  .contact-list {
    list-style: none;
    margin: 0;
    padding: 0;
    position: absolute;
    left: 40px;
    right: 60px;
    top: 60px;
  }
  .contact-item {
    display: flex;
    align-items: center;
    gap: 30px;
    height: 56px;
    border-bottom: 1.5px solid var(--rule);
    font-size: 21px;
    letter-spacing: 1px;
    color: var(--ink);
    white-space: nowrap;
  }
  .contact-item:last-child { border-bottom: none; }
  .contact-icon {
    width: 30px;
    height: 30px;
    border: 2px solid var(--icon-line);
    box-sizing: border-box;
    display: flex;
    align-items: center;
    justify-content: center;
    flex: none;
  }
  .contact-icon svg { width: 18px; height: 18px; }
</style>
</head>
<body>
  <div class="card">
    <div class="brand">
      <div class="brand-square"></div>
      <span class="brand-name">Tiskoro</span>
    </div>

    <div class="contact-frame">
      <div class="person">
        <p class="person-name">LEO MARSH</p>
        <p class="person-role">GENERAL MANAGER</p>
      </div>
      <ul class="contact-list">
        <li class="contact-item">
          <span class="contact-icon">
            <svg viewBox="0 0 24 24"><path d="M6 3h4l2 5-2.5 1.5a11 11 0 0 0 5 5L16 12l5 2v4a2 2 0 0 1-2 2A17 17 0 0 1 4 5a2 2 0 0 1 2-2z" fill="#e6d21f"/></svg>
          </span>
          012 478 3615
        </li>
        <li class="contact-item">
          <span class="contact-icon">
            <svg viewBox="0 0 24 24"><rect x="3" y="6" width="18" height="12" fill="none" stroke="#e6d21f" stroke-width="2"/><path d="M3 6l9 7 9-7" fill="none" stroke="#e6d21f" stroke-width="2"/></svg>
          </span>
          leo@tiskoro.com
        </li>
        <li class="contact-item">
          <span class="contact-icon">
            <svg viewBox="0 0 24 24"><circle cx="12" cy="12" r="9" fill="none" stroke="#e6d21f" stroke-width="2"/><path d="M3 12h18M12 3c3 3 3 15 0 18M12 3c-3 3-3 15 0 18" fill="none" stroke="#e6d21f" stroke-width="1.6"/></svg>
          </span>
          www.tiskoro.com
        </li>
        <li class="contact-item">
          <span class="contact-icon">
            <svg viewBox="0 0 24 24"><path d="M12 22s7-7 7-12a7 7 0 0 0-14 0c0 5 7 12 7 12z" fill="#e6d21f"/><circle cx="12" cy="10" r="2.5" fill="#fff"/></svg>
          </span>
          42 Orchard Lane, Unit 7, Kelmford
        </li>
      </ul>
    </div>
  </div>
</body>
</html>
```